Brody's Lot Grading & Trenching

I would like to have business cards created for my land clearing company. We have excavators, skid steers, dump trucks, tractor trailer dump trailers, forestry mulchers along with all size tractors for pasture restoration and arena builds.

Target Market(s)

Both commercial and residential clients

Contact Information for Business Card

Name, phone number, email and website

Colors

Designer to choose colors to be used in the design.

```html
<!DOCTYPE html>
<html lang="en">
<head>
<meta charset="utf-8">
<title>Brody's Lot Grading &amp; Trenching – Business Card</title>
<link rel="stylesheet" href="https://fonts.googleapis.com/css2?family=Oswald:wght@400;500;700&family=Poppins:wght@400;500&display=swap">
<style>
  :root {
    --page-bg: #c0bfc4;
    --title-orange: #f4915a;
    --card-black: #050505;
    --brand-yellow: #fcc419;
    --band-orange: #e0692a;
    --sky-blue: #3f7fb3;
    --sunset-orange: #f0902a;
    --earth-brown: #5a4630;
    --social-red: #e5342f;
    --text-white: #ffffff;
  }
  * { margin: 0; padding: 0; box-sizing: border-box; }
  html, body { width: 991px; height: 1200px; overflow: hidden; }
  body { background: var(--page-bg); position: relative; font-family: "Poppins", sans-serif; color: var(--text-white); }

  .sheet-title {
    position: absolute; top: 20px; left: 0; width: 991px; padding-left: 0;
    text-align: center; font-family: "Oswald", sans-serif; font-weight: 700;
    font-size: 54px; letter-spacing: 1px; color: var(--title-orange);
    text-shadow: 2px 2px 1px rgba(0,0,0,.35);
    transform: translateX(0);
  }
  .sheet-title span { display: inline-block; margin-left: 0; }

  .card { position: absolute; left: 88px; width: 817px; height: 467px; background: var(--card-black); overflow: hidden; }
  .card--front { top: 118px; }
  .card--back { top: 630px; }

  /* front */
  .front-photo {
    position: absolute; right: 0; top: 0; width: 560px; height: 100%;
    background:
      linear-gradient(180deg, transparent 55%, var(--earth-brown) 100%),
      radial-gradient(ellipse at 60% 30%, var(--sunset-orange) 0%, transparent 55%),
      linear-gradient(160deg, var(--sky-blue) 0%, #d98a3a 45%, #8a5a22 80%);
    -webkit-mask-image: linear-gradient(90deg, transparent 0%, #000 45%);
            mask-image: linear-gradient(90deg, transparent 0%, #000 45%);
  }
  .front-band {
    position: absolute; left: 0; top: 341px; width: 100%; height: 126px;
    background: linear-gradient(90deg, var(--band-orange) 0%, var(--band-orange) 45%, rgba(224,105,42,0) 80%);
  }
  .rule { position: absolute; left: 0; height: 3px; background: linear-gradient(90deg, var(--brand-yellow) 55%, rgba(252,196,25,0) 90%); }
  .front-rule-top { top: 118px; width: 100%; }
  .front-rule-band { top: 339px; width: 100%; }

  .brand { position: absolute; display: flex; align-items: center; gap: 10px; }
  .brand-name { font-family: "Oswald", sans-serif; font-weight: 400; font-size: 19px; line-height: 1.15; text-align: right; color: var(--text-white); }
  .brand-mark { width: 58px; height: 58px; border-radius: 50%; background: var(--brand-yellow); flex: none; }
  .card--front .brand { left: 72px; top: 46px; }
  .card--back .brand { right: 42px; top: 48px; }

  .service-list { position: absolute; top: 140px; list-style: none; font-size: 14.3px; line-height: 20.1px; }
  .service-list li { position: relative; padding-left: 19px; }
  .service-list li::before { content: "★"; position: absolute; left: 0; font-size: 10px; }
  .service-list--left { left: 32px; }
  .service-list--right { left: 234px; }

  .contact { position: absolute; left: 38px; }
  .contact-phone { font-family: "Oswald", sans-serif; font-weight: 700; font-size: 31px; line-height: 1.1; letter-spacing: .5px; }
  .contact-line { font-size: 16px; line-height: 23px; letter-spacing: .4px; }
  .card--front .contact { top: 348px; }
  .card--back .contact { top: 350px; }

  /* back */
  .back-photo {
    position: absolute; inset: 0;
    background:
      radial-gradient(ellipse at 50% 85%, rgba(140,80,20,.45) 0%, transparent 55%),
      linear-gradient(180deg, #0b0a08 0%, #1a140c 50%, #2a1f12 100%);
  }
  .back-rule { position: absolute; left: 0; width: 100%; height: 3px; background: var(--brand-yellow); }
  .back-rule--top { top: 117px; }
  .back-rule--bottom { top: 339px; }

  .owner { position: absolute; left: 38px; top: 40px; }
  .owner-name { font-family: "Oswald", sans-serif; font-weight: 700; font-size: 37px; line-height: 1.1; color: var(--brand-yellow); }
  .owner-role { font-size: 15px; letter-spacing: .5px; margin-top: -2px; }

  .service-area { position: absolute; left: 60px; width: 697px; top: 172px; text-align: center; }
  .service-area-title { font-family: "Oswald", sans-serif; font-weight: 700; font-size: 25px; color: var(--brand-yellow); letter-spacing: .5px; }
  .service-area-towns { margin-top: 8px; font-size: 16.5px; line-height: 23.3px; letter-spacing: .3px; }

  .social-links { position: absolute; right: 45px; top: 367px; display: flex; gap: 9px; }
  .social-dot { width: 46px; height: 46px; border-radius: 50%; background: var(--social-red); }
</style>
</head>
<body>
  <h1 class="sheet-title"><span>Final Revision</span></h1>

  <section class="card card--front">
    <div class="front-photo" role="img" aria-label="Photo of a yellow excavator on a dirt mound under a sunset sky"></div>
    <div class="front-band"></div>
    <div class="rule front-rule-top"></div>
    <div class="rule front-rule-band"></div>

    <div class="brand">
      <div class="brand-name">Brody's Lot Grading<br>&amp; Trenching, LLC</div>
      <div class="brand-mark"></div>
    </div>

    <ul class="service-list service-list--left">
      <li>Excavation Services</li>
      <li>Site Clearing</li>
      <li>Land Clearing</li>
      <li>Demolition Services</li>
      <li>Bobcat Services</li>
      <li>Shoring</li>
      <li>Land Demolition</li>
      <li>Grading Service</li>
      <li>Regrading</li>
    </ul>
    <ul class="service-list service-list--right">
      <li>Resloping</li>
      <li>Site Preparation</li>
      <li>Building Site Preparation</li>
      <li>Land Site Preparation</li>
      <li>Construction Demolition</li>
      <li>Forestry Mulching</li>
      <li>Pasture Reseeding</li>
      <li>Build Arenas</li>
      <li>Pasture Stump Removal</li>
    </ul>

    <div class="contact">
      <div class="contact-phone">(555)-014-2290</div>
      <div class="contact-line">brodyslotgrading@mailbox.com</div>
      <div class="contact-line">www.brodyslotgrading.com</div>
    </div>
  </section>

  <section class="card card--back">
    <div class="back-photo" role="img" aria-label="Darkened photo of two excavators silhouetted against a sunset"></div>
    <div class="back-rule back-rule--top"></div>
    <div class="back-rule back-rule--bottom"></div>

    <div class="owner">
      <div class="owner-name">Brody Hale</div>
      <div class="owner-role">Owner</div>
    </div>

    <div class="brand">
      <div class="brand-name">Brody's Lot Grading<br>&amp; Trenching, LLC</div>
      <div class="brand-mark"></div>
    </div>

    <div class="service-area">
      <h2 class="service-area-title">SERVICE AREA:</h2>
      <p class="service-area-towns">Brooksville, Bushnell, Dade City, Land O' Lakes, Lutz, Pasco County, San Antonio, Tampa, Webster, Weeki Wachee Gardens, Wesley Chapel, Zephyrhills</p>
    </div>

    <div class="contact">
      <div class="contact-phone">555-017-4836</div>
      <div class="contact-line">brodyslotgrading@mailbox.com</div>
      <div class="contact-line">www.brodyslotgrading.com</div>
    </div>

    <div class="social-links">
      <div class="social-dot"></div>
      <div class="social-dot"></div>
    </div>
  </section>
</body>
</html>
```